Southern Plantskills Academy needs a modern website that oozes professionalism

Our current website is boring and looks like everyone elses. We need a modern website that says we are the best at plant operator training. We use Brontovex and Hiraketo equipment for our training. We train all over Australia in Civil Construction, Mining and Quarrying. We want to be the "Go to" website for all plant operator training in Australia.

Industry/Entity Type

Heavy Machinery Training

Colors
0054AA
0677BA
7BADD7
CADEEF
E8F1F8
FFF300
FFF600
FEFA6F
FFFEC7
FFFEE8

```html
<!DOCTYPE html>
<html lang="en">
<head>
<meta charset="utf-8">
<title>Southern Plantskills Academy</title>
<link rel="stylesheet" href="https://fonts.googleapis.com/css2?family=Open+Sans:wght@400;600;700;800&family=Lato:wght@400;700&display=swap">
<style>
:root{
  --navy:#17396b;
  --navy-deep:#0f2a52;
  --ink:#1c2338;
  --yellow:#fbc70a;
  --text:#6b7280;
  --heading:#17396b;
  --light:#f4f6f9;
  --white:#ffffff;
  --line:#d7dbe2;
}
*{box-sizing:border-box;margin:0;padding:0}
html,body{width:1200px;height:4841px;overflow:hidden}
body{position:relative;font-family:"Lato",sans-serif;color:var(--text);background:var(--white)}
.abs{position:absolute}
h1,h2,h3,h4{font-family:"Open Sans",sans-serif}
.eyebrow{font-size:13px;color:var(--yellow);text-transform:uppercase;letter-spacing:.3px;text-decoration:underline;text-underline-offset:3px}
.section-title{font-size:42px;font-weight:700;color:var(--heading);line-height:1.2}
.btn{display:flex;align-items:center;justify-content:center;gap:12px;background:var(--yellow);color:var(--white);font-family:"Open Sans",sans-serif;font-weight:700;font-size:15px}
.btn svg{width:18px;height:18px}

/* top bar */
.topbar{left:0;top:0;width:1200px;height:47px;background:var(--ink);color:#c9ccd6;font-size:14px}
.topbar span{position:absolute;top:15px}
.topbar .dot{position:absolute;top:18px;width:12px;height:10px;border:2px solid var(--yellow);border-radius:2px}
.topbar .soc{position:absolute;top:18px;width:10px;height:10px;background:#9aa0b0;border-radius:2px}

/* header */
.header{left:0;top:47px;width:1200px;height:109px;background:var(--white)}
.brand{position:absolute;left:90px;top:35px;display:flex;align-items:center;gap:10px;font-family:"Open Sans",sans-serif;font-weight:800;color:var(--navy);font-size:17px;line-height:1.1}
.brand i{width:38px;height:38px;border-radius:50%;background:var(--navy);display:block}
.hinfo{position:absolute;top:30px;display:flex;gap:14px;font-size:14px;color:#333}
.hinfo small{display:block;color:var(--text);font-size:13px;margin-top:4px}
.hinfo svg{width:34px;height:34px}
.estimate{position:absolute;left:958px;top:28px;width:180px;height:49px;background:var(--navy);border-radius:4px;color:#fff;font-family:"Open Sans",sans-serif;font-weight:700;font-size:14px;display:flex;align-items:center;justify-content:center;gap:10px}

/* nav */
.nav{left:79px;top:156px;width:984px;height:66px;background:var(--white);display:flex;align-items:center;font-size:14px;color:#6b7280;z-index:3}
.nav a{position:absolute;text-decoration:none;color:inherit}
.nav a.active{color:var(--navy);font-weight:700}
.callbox{left:1063px;top:156px;width:74px;height:66px;background:var(--navy);display:flex;align-items:center;justify-content:center;z-index:3}

/* hero */
.hero{left:0;top:156px;width:1200px;height:800px}
.welcome{left:100px;top:451px;width:268px;height:41px;background:var(--navy);border-left:4px solid var(--yellow);color:#fff;font-family:"Open Sans",sans-serif;font-weight:700;font-size:20px;padding:6px 18px}
.hero h1{left:100px;top:520px;font-size:62px;font-weight:700;color:#fff;letter-spacing:.5px}
.hero-text{left:100px;top:610px;width:480px;color:#eef0f4;font-size:17px;line-height:1.6}

/* about */
.about-title{left:94px;top:1097px;width:520px}
.about-sub{left:94px;top:1222px;font-family:"Open Sans",sans-serif;font-weight:600;color:#1c2338;font-size:20px}
.para{font-size:13px;line-height:1.6;color:var(--text)}

/* services */
.services{left:0;top:1559px;width:1200px;height:648px;background:var(--light)}
.card{position:absolute;top:1767px;width:317px;height:355px;border-radius:4px;overflow:hidden}
.card h3{position:absolute;left:28px;top:231px;color:#fff;font-size:24px;font-weight:700}
.card h3::before{content:"";position:absolute;left:-4px;top:6px;width:18px;height:18px;border-radius:50%;background:var(--yellow);z-index:-1}
.card .go{position:absolute;left:28px;top:280px;width:50px;height:50px;border-radius:50%;background:rgba(255,255,255,.18);display:flex;align-items:center;justify-content:center}

/* experts */
.experts{left:0;top:2207px;width:1200px;height:385px}
.feature{position:absolute;top:2320px;width:231px;height:360px;background:#fff;box-shadow:0 6px 18px rgba(20,40,80,.12);text-align:center;padding-top:40px}
.feature h4{color:var(--navy);font-size:19px;font-weight:700;margin-top:18px}
.feature p{font-size:15px;line-height:1.65;margin:16px auto 0;width:170px}
.feature .more{margin-top:30px;color:var(--navy);font-family:"Open Sans",sans-serif;font-weight:700;font-size:14px}

/* testimonials */
.testi{left:0;top:3335px;width:1200px;height:534px;background:var(--navy-deep)}
.quote{position:absolute;top:3546px;width:322px;height:216px;background:#1e4279;border-radius:4px;padding:44px 32px 0;color:#dde3ee;font-size:13px;line-height:1.75}
.quote .q{position:absolute;left:50%;top:-12px;transform:translateX(-50%);color:var(--yellow);font-family:"Open Sans",sans-serif;font-weight:800;font-size:64px;line-height:1}
.person{display:flex;align-items:center;gap:14px;margin-top:16px}
.person i{width:48px;height:48px;border-radius:50%;background:linear-gradient(135deg,#c9b8a6,#6c5a4f);display:block}
.person b{display:block;color:#fff;font-family:"Open Sans",sans-serif;font-size:16px}
.person small{color:#8fa0bd;font-size:15px}

/* contact */
.citem{position:absolute;left:107px;display:flex;gap:28px;font-size:12.5px;color:var(--text)}
.citem b{display:block;color:#1c2338;font-family:"Open Sans",sans-serif;font-size:12.5px;margin-bottom:4px}
.citem i{width:38px;height:38px;border-radius:50%;background:#eef3fa;display:block}
.form{left:601px;top:3978px;width:494px;height:567px;background:#fff;border-top:5px solid var(--navy);box-shadow:0 4px 20px rgba(0,0,0,.08);z-index:4}
.form label{position:absolute;font-family:"Open Sans",sans-serif;font-weight:700;font-size:13px;color:#1c2338}
.field{position:absolute;border:1px solid #c5cad3;border-radius:20px;font-size:12px;color:#9aa0ab;padding:12px 24px}

/* footer */
.footer{left:0;top:4400px;width:1200px;height:441px}
.fitem{position:absolute;top:4612px;display:flex;gap:10px;color:#fff;font-size:13.5px;line-height:1.35}
.fnav{left:257px;top:4680px;width:721px;height:81px;border-top:1px solid #38507a;border-bottom:1px solid #38507a;display:flex;justify-content:space-around;align-items:center;color:#fff;font-size:14px;font-family:"Open Sans",sans-serif}
.sq{position:absolute;top:4791px;width:25px;height:25px;border:1px solid #fff}
.sq::after{content:"";position:absolute;left:7px;top:7px;width:9px;height:9px;background:#fff}
</style>
</head>
<body>

<!-- top bar -->
<div class="abs topbar">
  <i class="dot" style="left:78px;border-radius:50%"></i><span style="left:103px">Mon-Sat: 09am to 07:30pm</span>
  <i class="dot" style="left:325px"></i><span style="left:348px">hello@plantskills.example</span>
  <span style="left:866px;top:0;height:47px;border-left:1px solid #3a4157"></span>
  <span style="left:887px">Faqs</span><span style="left:954px">Pricing</span>
  <span style="left:1014px;top:0;height:47px;border-left:1px solid #3a4157"></span>
  <i class="soc" style="left:1036px"></i><i class="soc" style="left:1064px"></i><i class="soc" style="left:1093px"></i><i class="soc" style="left:1123px"></i>
</div>

<!-- header -->
<div class="abs header">
  <div class="brand"><i></i><span>Southern Plantskills<br>Academy</span></div>
  <div class="hinfo" style="left:362px">
    <svg viewBox="0 0 24 24" fill="none" stroke="#17396b" stroke-width="1.5"><path d="M5 4h4l2 5-3 2a11 11 0 0 0 5 5l2-3 5 2v4a2 2 0 0 1-2 2A17 17 0 0 1 3 6a2 2 0 0 1 2-2"/></svg>
    <div>+61-400-555-010<small>Need help? Make a Call</small></div>
  </div>
  <div class="hinfo" style="left:664px">
    <svg viewBox="0 0 24 24" fill="none" stroke="#17396b" stroke-width="1.5"><circle cx="12" cy="12" r="9"/><path d="M3 12h18M12 3c3 3 3 15 0 18M12 3c-3 3-3 15 0 18"/></svg>
    <div>Australia<small>212A Someplace somewhere</small></div>
  </div>
  <div class="estimate">Free Estimate
    <svg width="20" height="20" viewBox="0 0 24 24" fill="none" stroke="#fff" stroke-width="2"><circle cx="12" cy="12" r="10"/><path d="M8 12h8M13 8l4 4-4 4"/></svg>
  </div>
</div>

<!-- hero -->
<div class="abs hero">
  <div role="img" aria-label="Excavators loading a dump truck in a quarry" style="position:absolute;inset:0;background:linear-gradient(180deg,#5d564e 0%,#6e6358 45%,#4d4740 100%)"></div>
  <svg class="abs" style="left:0;top:640px" width="1200" height="320" viewBox="0 0 1200 320" preserveAspectRatio="none">
    <path d="M0 160 C 400 170 800 120 1200 0 L1200 320 L0 320 Z" fill="#fff"/>
    <path d="M0 150 C 300 175 550 170 700 140 C 520 180 300 200 0 200 Z" fill="var(--yellow)"/>
  </svg>
</div>
<nav class="abs nav">
  <a class="active" style="left:86px">Home</a>
  <a style="left:198px">About Us</a>
  <a style="left:311px">Services</a>
  <a style="left:423px">Gallery</a>
  <a style="left:542px">Our Team</a>
  <a style="left:692px">Contact Us</a>
</nav>
<div class="abs callbox">
  <svg width="40" height="40" viewBox="0 0 24 24" fill="none" stroke="#fff" stroke-width="1.3"><path d="M5 4h4l2 5-3 2a11 11 0 0 0 5 5l2-3 5 2v4a2 2 0 0 1-2 2A17 17 0 0 1 3 6a2 2 0 0 1 2-2"/></svg>
</div>
<div class="abs welcome">Welcome</div>
<h1 class="abs" style="left:100px;top:520px;font-size:62px;color:#fff;font-weight:700">Empowering Operators</h1>
<p class="abs hero-text">Lorem ipsum dolor sit amet, consectetur adipiscing elit, sed do eiusmod tempor i</p>
<div class="abs btn" style="left:100px;top:689px;width:176px;height:53px">Read More</div>

<!-- about -->
<div class="abs eyebrow" style="left:94px;top:1062px">Who we are</div>
<h2 class="abs section-title about-title">Training Operators for Industry Leaders</h2>
<div class="abs about-sub">Where Training Meets Transformation</div>
<p class="abs para" style="left:94px;top:1270px;width:505px">Lorem ipsum dolor sit amet, consectetur adipiscing elit, sed do eiusmod temp or incididunt ut labore et dolore magna aliqua. Ut enim ad minim veniam, quis laboris nisi ut aliquip ex ea commodo consequat.</p>
<p class="abs para" style="left:94px;top:1346px;width:505px">Lorem ipsum dolor sit amet, consectetur adipiscing elit, sed do eiusmod temp or incididunt ut labore et dolore magna aliqua.</p>
<div class="abs btn" style="left:92px;top:1427px;width:156px;height:47px">Contact us
  <svg viewBox="0 0 24 24" fill="none" stroke="#fff" stroke-width="2"><path d="M4 12h15M13 6l6 6-6 6"/></svg></div>
<div class="abs" role="img" aria-label="Yellow wheel loader cab" style="left:618px;top:1044px;width:233px;height:425px;background:linear-gradient(160deg,#2b3a2c,#c9a52c 60%,#dcc36a)"></div>
<div class="abs" role="img" aria-label="Operator in high-visibility gear guiding a loader" style="left:870px;top:1072px;width:234px;height:427px;background:linear-gradient(160deg,#8a8676,#6f6a5c 50%,#3a3a38)"></div>
<div class="abs" style="left:818px;top:1233px;width:80px;height:80px;border-radius:50%;background:var(--navy);border:4px solid #fff"></div>

<!-- services -->
<div class="abs services"></div>
<div class="abs eyebrow" style="left:90px;top:1619px">Our services</div>
<h2 class="abs section-title" style="left:86px;top:1650px">Services We Provide</h2>
<div class="abs" style="left:943px;top:1667px;font-size:15px;color:#1c2338">More Services</div>
<div class="abs" style="left:1076px;top:1658px;width:40px;height:38px;background:var(--yellow);display:flex;align-items:center;justify-content:center">
  <svg width="14" height="14" viewBox="0 0 10 10"><path d="M3 1l4 4-4 4z" fill="#fff"/></svg></div>

<div class="card" style="left:98px" role="img" aria-label="Civil construction worker beside an excavator">
  <div style="position:absolute;inset:0;background:linear-gradient(180deg,#c79a2a 0%,#6d5a3a 45%,#141414 100%)"></div>
  <h3>Civil Construction</h3>
  <div class="go"><svg width="18" height="18" viewBox="0 0 24 24" fill="none" stroke="#fff" stroke-width="2"><path d="M4 12h15M13 6l6 6-6 6"/></svg></div>
</div>
<div class="card" style="left:443px" role="img" aria-label="Mining worker in a hard hat">
  <div style="position:absolute;inset:0;background:linear-gradient(180deg,#b8a27c 0%,#6d6455 45%,#141414 100%)"></div>
  <h3>Mining</h3>
  <div class="go"><svg width="18" height="18" viewBox="0 0 24 24" fill="none" stroke="#fff" stroke-width="2"><path d="M4 12h15M13 6l6 6-6 6"/></svg></div>
</div>
<div class="card" style="left:791px" role="img" aria-label="Excavator bucket digging in a quarry">
  <div style="position:absolute;inset:0;background:linear-gradient(180deg,#c99656 0%,#8a6030 45%,#141414 100%)"></div>
  <h3>Quarrying</h3>
  <div class="go"><svg width="18" height="18" viewBox="0 0 24 24" fill="none" stroke="#fff" stroke-width="2"><path d="M4 12h15M13 6l6 6-6 6"/></svg></div>
</div>

<!-- leading experts -->
<div class="abs experts" role="img" aria-label="Workers on a construction site" style="background:linear-gradient(90deg,#2a2925,#3e3a33 50%,#2c2a26)"></div>
<h2 class="abs" style="left:92px;top:2318px;font-size:41px;line-height:1.25;color:#fff;font-weight:700">Leading<br>Experts</h2>
<div class="abs btn" style="left:92px;top:2485px;width:156px;height:47px">Contact us
  <svg viewBox="0 0 24 24" fill="none" stroke="#fff" stroke-width="2"><path d="M4 12h15M13 6l6 6-6 6"/></svg></div>

<div class="feature" style="left:355px">
  <svg width="44" height="44" viewBox="0 0 24 24" fill="none" stroke="#17396b" stroke-width="1.3"><circle cx="12" cy="12" r="3.2"/><path d="M12 2l2 3 3.5-1 .5 3.5 3 2-2 3 2 3-3 2-.5 3.5-3.5-1-2 3-2-3-3.5 1L6 18l-3-2 2-3-2-3 3-2 .5-3.5L10 5z"/></svg>
  <h4>Expertise</h4>
  <p>Lorem ipsum dolor sit consectetur adipiscing elit, sed do eiusmod tempor incididunt</p>
  <div class="more">Read More &nbsp;→</div>
</div>
<div class="feature" style="left:614px">
  <svg width="44" height="44" viewBox="0 0 24 24" fill="none" stroke="#17396b" stroke-width="1.3"><circle cx="11" cy="11" r="8"/><circle cx="11" cy="11" r="3"/><circle cx="17" cy="17" r="4" fill="#fff"/><path d="M15.5 17l1 1 2-2"/></svg>
  <h4>Professional</h4>
  <p>Lorem ipsum dolor sit consectetur adipiscing elit, sed do eiusmod tempor incididunt</p>
  <div class="more">Read More &nbsp;→</div>
</div>
<div class="feature" style="left:875px">
  <svg width="44" height="44" viewBox="0 0 24 24" fill="none" stroke="#17396b" stroke-width="1.3"><circle cx="12" cy="7" r="4"/><path d="M4 21v-2a5 5 0 0 1 5-5h6a5 5 0 0 1 5 5v2z"/></svg>
  <h4>Experienced</h4>
  <p>Lorem ipsum dolor sit consectetur adipiscing elit, sed do eiusmod tempor incididunt</p>
  <div class="more">Read More &nbsp;→</div>
</div>

<!-- gallery -->
<div class="abs eyebrow" style="left:0;width:1200px;text-align:center;top:2741px">Our gallery</div>
<h2 class="abs section-title" style="left:0;width:1200px;text-align:center;top:2772px">Our Latest Projects</h2>
<div class="abs" role="img" aria-label="Excavator on a muddy building site" style="left:0;top:2879px;width:222px;height:379px;background:linear-gradient(180deg,#7b8088,#5e5548 50%,#4a3f34)"></div>
<div class="abs" role="img" aria-label="Wheel loader at sunset on a project site" style="left:229px;top:2879px;width:740px;height:379px;background:linear-gradient(180deg,#4c5260,#3c3b38 55%,#2a2824)"></div>
<div class="abs" role="img" aria-label="Smiling worker in safety vest and hard hat" style="left:977px;top:2879px;width:223px;height:379px;background:linear-gradient(180deg,#a9b4bd,#b3a24a 55%,#39457a)"></div>
<h3 class="abs" style="left:229px;width:740px;text-align:center;top:3000px;color:#fff;font-size:37px;line-height:1.35;font-weight:700">Latest Project in<br>Melbourne</h3>
<p class="abs" style="left:409px;width:380px;text-align:center;top:3125px;color:#e3e5ea;font-size:12.5px;line-height:1.6">Lorem ipsum dolor sit amet, consectetur adipiscing elit, sed do eiusmod tempor incidid</p>
<div class="abs" style="left:254px;top:3050px;width:38px;height:38px;border-radius:50%;background:#fff;display:flex;align-items:center;justify-content:center"><svg width="16" height="16" viewBox="0 0 24 24" fill="none" stroke="#1c2338" stroke-width="2.4"><path d="M20 12H5M11 6l-6 6 6 6"/></svg></div>
<div class="abs" style="left:906px;top:3050px;width:38px;height:38px;border-radius:50%;background:#fff;display:flex;align-items:center;justify-content:center"><svg width="16" height="16" viewBox="0 0 24 24" fill="none" stroke="#1c2338" stroke-width="2.4"><path d="M4 12h15M13 6l6 6-6 6"/></svg></div>

<!-- testimonials -->
<div class="abs testi"></div>
<div class="abs eyebrow" style="left:0;width:1200px;text-align:center;top:3389px;text-decoration:none">Testimonials</div>
<h2 class="abs" style="left:0;width:1200px;text-align:center;top:3420px;color:#fff;font-size:41px;font-weight:700">What Clients are Saying</h2>
<div class="quote" style="left:92px"><span class="q">”</span>Lorem ipsum dolor sit amet, consectetur adipiscing elit, sed do eiusmod tempor i ncididunt ut labore et dolore magna aliq ua. Ut enim ad minim veniam, quis nostr
  <div class="person"><i></i><div><b>Jordan M.</b><small>Country</small></div></div></div>
<div class="quote" style="left:439px"><span class="q">”</span>Lorem ipsum dolor sit amet, consectetur adipiscing elit, sed do eiusmod tempor i ncididunt ut labore et dolore magna aliq ua. Ut enim ad minim veniam, quis nostr
  <div class="person"><i></i><div><b>Jordan M.</b><small>Country</small></div></div></div>
<div class="quote" style="left:785px"><span class="q">”</span>Lorem ipsum dolor sit amet, consectetur adipiscing elit, sed do eiusmod tempor i ncididunt ut labore et dolore magna aliq ua. Ut enim ad minim veniam, quis nostr
  <div class="person"><i></i><div><b>Jordan M.</b><small>Country</small></div></div></div>
<svg class="abs" style="left:560px;top:3784px" width="80" height="16" viewBox="0 0 80 16">
  <circle cx="8" cy="8" r="3" fill="#c9d3e3"/><circle cx="24" cy="8" r="3" fill="#c9d3e3"/>
  <circle cx="40" cy="8" r="5" fill="none" stroke="#c9d3e3"/><circle cx="40" cy="8" r="2.5" fill="#c9d3e3"/>
  <circle cx="56" cy="8" r="3" fill="#c9d3e3"/><circle cx="72" cy="8" r="3" fill="#c9d3e3"/>
</svg>

<!-- contact -->
<h2 class="abs" style="left:107px;top:3975px;font-size:42px;color:var(--heading)"><b style="font-weight:700">Contact Us</b> <span style="font-weight:400">Today</span></h2>
<div class="citem" style="top:4056px"><i></i><div><b>HEAD OFFICE</b>21 Lorem Ipsum, ABC 123</div></div>
<div class="citem" style="top:4131px"><i></i><div><b>EMAIL ADDRESS</b>name@company.com</div></div>
<div class="citem" style="top:4197px"><i></i><div><b>CALL US NOW</b>Call Now: 123-456-789</div></div>

<!-- footer background -->
<svg class="abs" style="left:0;top:4280px" width="1200" height="561" viewBox="0 0 1200 561" preserveAspectRatio="none">
  <path d="M0 260 C 300 170 700 110 1200 100 L1200 561 L0 561 Z" fill="#0f2347"/>
  <path d="M390 190 C 600 130 900 90 1200 85 L1200 60 C 900 70 600 120 390 190 Z" fill="var(--yellow)"/>
</svg>

<div class="abs form">
  <h3 style="position:absolute;left:39px;top:52px;color:#1c2338;font-size:25px;font-weight:700">Send A Message</h3>
  <label style="left:39px;top:116px">First Name</label>
  <div class="field" style="left:39px;top:135px;width:198px;height:41px">John</div>
  <label style="left:252px;top:116px">Last Name</label>
  <div class="field" style="left:252px;top:135px;width:197px;height:41px">Doe</div>
  <label style="left:39px;top:202px">Email</label>
  <div class="field" style="left:39px;top:223px;width:417px;height:40px">info@company.com</div>
  <label style="left:39px;top:292px">Message</label>
  <div class="field" style="left:39px;top:311px;width:417px;height:123px;border-radius:4px">Type Your Message</div>
  <div class="btn" style="position:absolute;left:39px;top:475px;width:155px;height:43px">Contact us
    <svg viewBox="0 0 24 24" fill="none" stroke="#fff" stroke-width="2"><path d="M4 12h15M13 6l6 6-6 6"/></svg></div>
</div>

<div class="abs brand" style="left:118px;top:4615px;color:#fff;font-size:17px;display:flex;align-items:center;gap:10px;font-family:'Open Sans',sans-serif;font-weight:800;line-height:1.1"><i style="width:38px;height:38px;border-radius:50%;background:#fff;display:block"></i><span>Southern Plantskills<br>Academy</span></div>
<div class="abs" style="left:410px;top:4612px;height:44px;border-left:1px solid #38507a"></div>
<div class="fitem" style="left:432px"><svg width="26" height="26" viewBox="0 0 24 24" fill="none" stroke="#fff" stroke-width="1.4"><circle cx="12" cy="12" r="9"/><path d="M3 12h18M12 3c3 3 3 15 0 18M12 3c-3 3-3 15 0 18"/></svg><div>123, Building Name, Street<br>City, State XY 123456</div></div>
<div class="abs" style="left:669px;top:4612px;height:44px;border-left:1px solid #38507a"></div>
<div class="fitem" style="left:689px"><svg width="26" height="26" viewBox="0 0 24 24" fill="none" stroke="#fff" stroke-width="1.4"><rect x="6" y="2" width="11" height="20" rx="2"/><path d="M19 9c1 1 1 5 0 6"/></svg><div>PHONE<br>(123) 456 7890</div></div>
<div class="abs" style="left:846px;top:4612px;height:44px;border-left:1px solid #38507a"></div>
<div class="fitem" style="left:866px"><svg width="26" height="26" viewBox="0 0 24 24" fill="none" stroke="#fff" stroke-width="1.4"><rect x="3" y="6" width="18" height="14"/><path d="M3 6l9 7 9-7"/></svg><div>EMAIL<br>info@company.com</div></div>

<nav class="abs fnav"><span>HOME</span><span>SERVICES</span><span>ABOUT US</span><span>TESTIMONIALS</span><span>BLOG</span><span>CONTACT US</span></nav>
<div class="abs" style="left:135px;top:4795px;color:#fff;font-size:12px;font-family:'Open Sans',sans-serif">Southern Plantskills Academy</div>
<div class="sq" style="left:933px"></div><div class="sq" style="left:966px"></div><div class="sq" style="left:999px"></div><div class="sq" style="left:1032px"></div>

</body>
</html>
```